"Cedar Hollow Realty" is the name of my real estate company

This is for a: "for sale" sign, looking for a minimalist design, wire frame outline of a midcentury modern homes roof line or elevation?

My name is: Dean Marlowe (needed)
My Cell # is: 415 208 3947 (needed)
My BRE license # is: 02468135 (needed)
BRE needs to be displayed in this format: BRE 02468135 (needed)
The white outline on the sign riders 'pictured" may work on large sign
Note font on pictured rider sign

This design is for a real estate "for sale" sign or sandwich board sign. Do Not include the words "For Sale" on the sign.

The measurements are 36" inches (91.44 cm) Length, or tall X 24" inches (60.90 cm) Wide.

|
3
---- 24 ----
6
|

Sorry I wasn't more specific earlier. I'd like the elements of the sign to be scaled in size according to their importance, from largest to smallest:

My name: Dean Marlowe
My phone number: 415-208-3947
My company name: Cedar Hollow Realty
My license number: BRE 02468135 (This can be much smaller than the smallest text)
Additionally, please incorporate contemporary to mid-century modern elements on the wire frame roofline or a simple roof-like design.

Thank you!

Best regards,
Dean

```html
<!DOCTYPE html>
<html lang="en">
<head>
<meta charset="UTF-8">
<title>Cedar Hollow Realty – Yard Sign</title>
<link rel="stylesheet" href="https://fonts.googleapis.com/css2?family=Poppins:wght@400;700&display=swap">
<style>
  :root {
    --backdrop: #cfcfcf;
    --sign-black: #000000;
    --ink-white: #ffffff;
    --rule-grey: #8a8a8a;
    --roof-tone-a: #2a2a2a;
    --roof-tone-b: #111111;
  }
  * { margin: 0; padding: 0; box-sizing: border-box; }
  html, body {
    width: 867px;
    height: 1200px;
    overflow: hidden;
    background: var(--backdrop);
  }
  .sign {
    position: absolute;
    left: 33.5px;
    top: 0;
    width: 800px;
    height: 1200px;
    background: var(--sign-black);
    font-family: "Poppins", sans-serif;
    color: var(--ink-white);
  }
  .sign__frame {
    position: absolute;
    left: 65.6px;
    top: 65.6px;
    width: 670.4px;
    height: 1070.4px;
    border: 2px solid var(--ink-white);
  }
  .line {
    position: absolute;
    left: 0;
    width: 100%;
    text-align: center;
    line-height: 1;
    white-space: nowrap;
  }
  .company__main {
    top: 298px;
    font-size: 56px;
    font-weight: 700;
    letter-spacing: 0.5px;
  }
  .company__sub {
    top: 374px;
    font-size: 64px;
    font-weight: 400;
  }
  .agent-name {
    top: 516px;
    font-size: 80px;
    font-weight: 400;
  }
  .rule {
    position: absolute;
    left: 136px;
    width: 528px;
    height: 2px;
    background: linear-gradient(to right, transparent, var(--rule-grey) 15%, var(--ink-white) 50%, var(--rule-grey) 85%, transparent);
  }
  .rule--top { top: 635px; }
  .rule--bottom { top: 745px; }
  .phone {
    top: 657px;
    display: flex;
    justify-content: center;
    align-items: center;
    gap: 16px;
    font-size: 57px;
    font-weight: 400;
  }
  .phone__icon {
    width: 44px;
    height: 44px;
    flex: none;
    margin-top: -4px;
  }
  .license {
    top: 779px;
    font-size: 31px;
    font-weight: 400;
  }
  .roofline {
    position: absolute;
    left: 116px;
    top: 966px;
    width: 564px;
    height: 170px;
    background: linear-gradient(to bottom, var(--roof-tone-a), var(--roof-tone-b));
  }
</style>
</head>
<body>
  <main class="sign">
    <div class="sign__frame"></div>

    <div class="line company__main">CEDAR HOLLOW</div>
    <div class="line company__sub">REALTY</div>

    <div class="line agent-name">DEAN MARLOWE</div>

    <div class="rule rule--top"></div>
    <div class="line phone">
      <svg class="phone__icon" viewBox="0 0 44 44" aria-hidden="true">
        <circle cx="22" cy="22" r="22" fill="#ffffff"/>
        <path d="M15.5 11.5c1-.8 2.3-.6 3 .4l2.3 3.3c.6.9.5 2-.3 2.7l-1.6 1.3c.9 2.3 2.8 4.4 5.2 5.6l1.4-1.5c.7-.8 1.9-.9 2.7-.2l3.2 2.5c1 .8 1.1 2.2.3 3.1l-1.4 1.6c-1.2 1.3-3.1 1.7-4.7 1-6.1-2.6-10.6-7.4-12.8-13.6-.6-1.6-.1-3.4 1.2-4.5z" fill="#000000"/>
        <path d="M24 12.5a8 8 0 0 1 7.5 7.5M24 16.5a4 4 0 0 1 3.5 3.5" stroke="#000000" stroke-width="1.8" fill="none" stroke-linecap="round"/>
      </svg>
      <span class="phone__number">415-208-3947</span>
    </div>
    <div class="rule rule--bottom"></div>

    <div class="line license">BRE 02468135</div>

    <div class="roofline" role="img" aria-label="White wire-frame outline of a mid-century modern roofline with chimney"></div>
  </main>
</body>
</html>
```